Vision, Mission and Culture Posters

We have written text paragraphs for our company vision and mission and need them made into a2 or a3 sized posters using our logo for inspiration for colour. Our company culture has 10 paragraphs and we'd like this to be a single poster of a2 or a1. Each poster should have the logo on and share common design. It's not a complex job really.

Industry/Entity Type

It Company

Requirements
Nice to have
• These will be going up on our office wall so need to be clear to read from a distance and look professional but also not stodgy.

```html
<!DOCTYPE html>
<html lang="en">
<head>
<meta charset="utf-8">
<title>Company Values – Kerbside Bay Hire</title>
<link href="https://fonts.googleapis.com/css2?family=Anton&family=Oswald:wght@700&family=Lato:wght@400;700;900&display=swap" rel="stylesheet">
<style>
  :root {
    --yellow: #fff200;
    --black: #0a0a0a;
    --red: #d2232a;
    --paper: #f4f4f2;
    --paper-edge: #e4e4e2;
    --ink: #1c1c1c;
    --badge-line: #3a3a3a;
  }
  * { margin: 0; padding: 0; box-sizing: border-box; }
  html, body { width: 1200px; height: 847px; overflow: hidden; }
  body { background: var(--paper); font-family: "Lato", Arial, sans-serif; color: var(--ink); }
  .poster {
    position: relative; width: 1200px; height: 847px; overflow: hidden;
    background: radial-gradient(ellipse at 50% 55%, #ffffff 0%, var(--paper) 55%, var(--paper-edge) 100%);
  }
  .poster__bands { position: absolute; inset: 0; }
  .brand {
    position: absolute; left: 54px; top: 18px; width: 346px; height: 103px;
    background: var(--yellow); border: 5px solid var(--black); border-radius: 14px;
    display: flex; align-items: center; gap: 14px; padding-left: 24px;
  }
  .brand__mark { width: 26px; height: 26px; background: var(--red); flex: none; }
  .brand__name {
    font-family: "Lato", Arial, sans-serif; font-weight: 900; font-size: 27px;
    line-height: 1.1; color: var(--black); letter-spacing: 0.5px;
  }
  .title {
    position: absolute; left: 425px; top: 24px; width: 632px; height: 98px;
    background: var(--black); border-radius: 12px;
    display: flex; align-items: center; justify-content: center;
  }
  .title__text {
    font-family: "Anton", Impact, sans-serif; font-size: 86px; line-height: 1;
    color: var(--yellow); letter-spacing: 1px; padding-top: 4px;
  }
  .value { position: absolute; }
  .value--left { left: 18px; width: 570px; }
  .value--right { left: 617px; width: 566px; }
  .value__badge { position: absolute; left: 0; top: 0; width: 40px; height: 48px; }
  .value__badge text {
    font-family: "Oswald", Impact, sans-serif; font-weight: 700; font-size: 24px; fill: var(--red);
  }
  .value__heading {
    margin-left: 50px; font-family: "Oswald", Impact, sans-serif; font-weight: 700;
    font-size: 37px; line-height: 48px; letter-spacing: 1.2px; color: var(--black);
    text-transform: uppercase;
  }
  .value__text {
    margin-left: 57px; margin-top: 4px; font-size: 11.3px; line-height: 15.4px; text-align: justify;
  }
  .value--right .value__heading { margin-left: 47px; }
  .value--right .value__text { margin-left: 54px; }
</style>
</head>
<body>
<main class="poster">
  <svg class="poster__bands" width="1200" height="847" viewBox="0 0 1200 847" aria-hidden="true">
    <path d="M0 0 H1200 V14 L1070 146 Q1050 150 1000 148 Q500 132 0 138 Z" fill="var(--yellow)"/>
    <path d="M0 138 Q500 132 1000 148 Q1050 150 1070 146 L1200 14" fill="none" stroke="var(--black)" stroke-width="2"/>
    <path d="M0 838 Q600 815 1180 818 Q1196 820 1200 826 V847 H0 Z" fill="var(--red)"/>
    <path d="M0 838 Q600 815 1180 818 Q1196 820 1200 826" fill="none" stroke="var(--black)" stroke-width="2"/>
  </svg>

  <div class="brand">
    <span class="brand__mark"></span>
    <span class="brand__name">Kerbside<br>Bay Hire</span>
  </div>

  <header class="title"><h1 class="title__text">COMPANY VALUES</h1></header>

  <section class="value value--left" style="top:152px">
    <svg class="value__badge" viewBox="0 0 40 48"><path d="M5 2 H26 L38 20 V28 L26 46 H5 Q2 46 2 43 V5 Q2 2 5 2 Z" fill="#fff" stroke="var(--badge-line)" stroke-width="1.6"/><text x="17" y="34" text-anchor="middle">01</text></svg>
    <h2 class="value__heading">Communication</h2>
    <p class="value__text">We believe in open communication providing our customers, colleagues and others with honest, accurate, concise and prompt information relevant to their needs to ensure everyone always has a sound understanding of any matter being communicated. We are polite, friendly and warm and we use good communication as a means of enhancing our customer experience.</p>
  </section>

  <section class="value value--left" style="top:287px">
    <svg class="value__badge" viewBox="0 0 40 48"><path d="M5 2 H26 L38 20 V28 L26 46 H5 Q2 46 2 43 V5 Q2 2 5 2 Z" fill="#fff" stroke="var(--badge-line)" stroke-width="1.6"/><text x="17" y="34" text-anchor="middle">02</text></svg>
    <h2 class="value__heading">Education</h2>
    <p class="value__text">We believe in the importance of continual learning and education and thrive on helping our colleagues by sharing our knowledge and learnings. We learn from our mistakes and use them to build a better, stronger, closer team environment. Understanding that everyone's needs are different and that we learn in different ways, we challenge our people to constantly improve their professional development in a way that works best for them.</p>
  </section>

  <section class="value value--left" style="top:432px">
    <svg class="value__badge" viewBox="0 0 40 48"><path d="M5 2 H26 L38 20 V28 L26 46 H5 Q2 46 2 43 V5 Q2 2 5 2 Z" fill="#fff" stroke="var(--badge-line)" stroke-width="1.6"/><text x="17" y="34" text-anchor="middle">03</text></svg>
    <h2 class="value__heading">Professionalism</h2>
    <p class="value__text">We represent ourselves as professionals and our business to the best of our abilities at all times taking particular care to give the best impression of ourselves to those we interact with during the course of our working days whether that be by phone, email or in person. We are always on time, well presented, well prepared and work hard to succeed.</p>
  </section>

  <section class="value value--left" style="top:567px">
    <svg class="value__badge" viewBox="0 0 40 48"><path d="M5 2 H26 L38 20 V28 L26 46 H5 Q2 46 2 43 V5 Q2 2 5 2 Z" fill="#fff" stroke="var(--badge-line)" stroke-width="1.6"/><text x="17" y="34" text-anchor="middle">04</text></svg>
    <h2 class="value__heading">Ownership</h2>
    <p class="value__text">We are each fully responsible for our roles and for our contribution to the success of our business. We are accountable for our results, our ability to improve at what we do, our mistakes and what we do to correct them.</p>
  </section>

  <section class="value value--left" style="top:688px">
    <svg class="value__badge" viewBox="0 0 40 48"><path d="M5 2 H26 L38 20 V28 L26 46 H5 Q2 46 2 43 V5 Q2 2 5 2 Z" fill="#fff" stroke="var(--badge-line)" stroke-width="1.6"/><text x="17" y="34" text-anchor="middle">05</text></svg>
    <h2 class="value__heading">Commercial Awareness</h2>
    <p class="value__text">We understand that in a small business everything we do can impact the success of our business and we commit ourselves to thinking about the impact on our business of all the decisions we make before we make them. We consider cost against benefit, remembering the cheapest option doesn't always give the greatest benefit, the best value use of our time, who benefits from what we do and how it benefits our business.</p>
  </section>

  <section class="value value--right" style="top:156px">
    <svg class="value__badge" viewBox="0 0 40 48"><path d="M5 2 H26 L38 20 V28 L26 46 H5 Q2 46 2 43 V5 Q2 2 5 2 Z" fill="#fff" stroke="var(--badge-line)" stroke-width="1.6"/><text x="17" y="34" text-anchor="middle">06</text></svg>
    <h2 class="value__heading">Balance</h2>
    <p class="value__text">We try to find the best balance in our lives between our responsibilities, obligations, duties and desires whilst still ensuring we have time to devote to friends, families, fun and life. We try to balance our opinions and thoughts with those of others and believe that with balance comes fairness, integrity, self-control and a great attitude.</p>
  </section>

  <section class="value value--right" style="top:291px">
    <svg class="value__badge" viewBox="0 0 40 48"><path d="M5 2 H26 L38 20 V28 L26 46 H5 Q2 46 2 43 V5 Q2 2 5 2 Z" fill="#fff" stroke="var(--badge-line)" stroke-width="1.6"/><text x="17" y="34" text-anchor="middle">07</text></svg>
    <h2 class="value__heading">Customer Service</h2>
    <p class="value__text">We believe that without our customers we would not be successful and understand the outstanding level of service we give them is critical to our continued success, even down to the smallest action whenever that may be required from us. We go out of our way to help any customer with an issue and are only satisfied when we have helped them achieve a fair outcome they are happy with.</p>
  </section>

  <section class="value value--right" style="top:425px">
    <svg class="value__badge" viewBox="0 0 40 48"><path d="M5 2 H26 L38 20 V28 L26 46 H5 Q2 46 2 43 V5 Q2 2 5 2 Z" fill="#fff" stroke="var(--badge-line)" stroke-width="1.6"/><text x="17" y="34" text-anchor="middle">08</text></svg>
    <h2 class="value__heading">Consistency</h2>
    <p class="value__text">We believe in consistency of our work, our approach, our positive attitude and our actions to set a standard at which our colleagues and customers feel a level of familiarity that strengthens our relationship whilst representing ourselves and our business to their best.</p>
  </section>

  <section class="value value--right" style="top:545px">
    <svg class="value__badge" viewBox="0 0 40 48"><path d="M5 2 H26 L38 20 V28 L26 46 H5 Q2 46 2 43 V5 Q2 2 5 2 Z" fill="#fff" stroke="var(--badge-line)" stroke-width="1.6"/><text x="17" y="34" text-anchor="middle">09</text></svg>
    <h2 class="value__heading">Success</h2>
    <p class="value__text">We understand success isn't given, it is earned every day, piece by piece. We are driven to succeed as an individual and as a team and we support each other in earning that success. We are not afraid to celebrate our successes to acknowledge our hard work and dedication to our achieving our goals.</p>
  </section>

  <section class="value value--right" style="top:665px">
    <svg class="value__badge" viewBox="0 0 40 48"><path d="M5 2 H26 L38 20 V28 L26 46 H5 Q2 46 2 43 V5 Q2 2 5 2 Z" fill="#fff" stroke="var(--badge-line)" stroke-width="1.6"/><text x="17" y="34" text-anchor="middle">10</text></svg>
    <h2 class="value__heading">Commitment</h2>
    <p class="value__text">We are committed to the company vision, to the mission and to upholding the company culture as well as showing the company the same commitment it has shown to us. We talk about our vision, mission and culture often, use them to help guide ourselves and our colleagues as we go about our work. We are not afraid to let our colleagues know when we feel they are not showing the right commitment to our vision, mission and culture but make sure we do so in a positive and helpful way to ensure they can get back on track as easily as possible.</p>
  </section>
</main>
</body>
</html>
```